my website is tavorinque.com. (brand name is ta belle vitrine) This is just a template that i have choose for. The content and the pictures are not about my business just the template.
I would like to have 4 pages for now. 1 homepage, which will be an overview for all pages, it is right now in this way. It will directly highlight my story. My website will tell an exclusive story about details which makes the difference and will make people happy with very small things. It will be art related but very stylish as well. I also want to have a event agenda on my homepage where people can see where my next event is. Page 2 my blog, where I will write weekly about mindset, lifestyle and details. Inspiration place for people who are looking for unique and exclusive approaches in life. Page 3 shop, where I will sell my stuff which is handmade and unique, it will be limited edition stuff. Mostly I will make the designs from marbling art, which I am a teacher for. (https://www.vidoranta.com/watch?v=KpwuzRaxTmo) check this video out for more. Page 4 is book page. Here people will be able to book private or group classes for marbling art (check the video). I have already a community of more than 500 people on gath rix, which will be my public as well. I wanna implement the gath rix button on this page as well. to be able to track.

This is about my website. I also need a logo for my brand, which will suit my website and my goals.

I can also give you a reference website, which really like as structure and style;
https://www.brightorvalco.com/products/the-morning-ledger?gclid=Xr4TpLmwq2HsVD9KEBsZTrc-WkPhyQ-uvlEjdRs3NKaOYFCBWMpuTzG8xyCVbhdnLWRqoaNf_2e8ZtpRvHbAwq9FLQ_hqgQ

Logo Text

ta belle vitrine

Coding

Coded - Design and coding required

Number of Pages Required

4 page

Requirements
Must have
• I can also give you a reference website, which really like as structure and style;
• https://www.brightorvalco.com/products/the-morning-ledger?gclid=Xr4TpLmwq2HsVD9KEBsZTrc-WkPhyQ-uvlEjdRs3NKaOYFCBWMpuTzG8xyCVbhdnLWRqoaNf_2e8ZtpRvHbAwq9FLQ_hqgQ

```html
<!DOCTYPE html>
<html lang="en">
<head>
<meta charset="utf-8">
<title>ta belle vitrine — Home</title>
<link rel="stylesheet" href="https://fonts.googleapis.com/css2?family=Montserrat:wght@400;600;700;800&family=Open+Sans:wght@400;600;700&family=Rufina:wght@700&display=swap">
<style>
:root{
  --ink:#111111;
  --dark:#1d1d1d;
  --black:#000000;
  --white:#ffffff;
  --paper:#f4f4f4;
  --hero-bg:#eeeeee;
  --muted:#666666;
  --line:#dddddd;
  --star:#f0a21c;
  --orange:#f08a12;
  --footer-text:#cfcfcf;
  --body:"Open Sans",Arial,sans-serif;
  --sans:"Montserrat",Arial,sans-serif;
  --display:"Rufina",Georgia,serif;
}
*{box-sizing:border-box;margin:0;padding:0}
html,body{width:1200px;height:4433px;overflow:hidden}
body{font-family:var(--body);color:var(--ink);background:var(--white);position:relative}
.wrap{position:absolute;left:248px;width:706px}
.btn{display:inline-block;background:var(--ink);color:var(--white);font:600 12px var(--body);padding:12px 26px;text-decoration:none}
.btn-light{background:var(--white);color:var(--ink);border:1px solid #bbb}
.stars{color:var(--star);font-size:13px;letter-spacing:1px}
.section-title{font:700 48px var(--display);text-align:center;letter-spacing:1px;color:var(--ink)}
.section-sub{font:400 17px/1.35 var(--body);color:var(--muted);text-align:center;width:420px;margin:6px auto 0}
.ph{position:absolute;display:block}

/* top bar */
.topbar{position:absolute;top:0;left:0;width:1200px;height:30px;background:var(--ink);color:#ddd;font-size:10px}
.topbar .contact{position:absolute;left:248px;top:9px}
.topbar .contact b{color:var(--white);margin-right:4px}
.topbar .contact span{margin-right:20px}
.dots{position:absolute;display:flex;gap:7px}
.dots i{width:13px;height:13px;border-radius:50%;background:#bdbdbd;display:block}
.topbar .dots{right:248px;top:8px}

/* header */
.header{position:absolute;top:30px;left:0;width:1200px;height:74px;background:var(--white)}
.brand{position:absolute;left:248px;top:22px;display:flex;align-items:center;gap:10px;font:600 20px var(--body);color:var(--ink)}
.brand i{width:26px;height:26px;border:2px solid var(--ink);border-radius:50%;display:block}
.nav{position:absolute;right:248px;top:28px;display:flex;gap:24px;font:400 13px var(--body);align-items:center}
.nav a{color:var(--ink);text-decoration:none}

/* hero */
.hero{position:absolute;top:104px;left:0;width:1200px;height:463px;background:var(--hero-bg);overflow:hidden}
.hero-art{right:0;top:0;width:660px;height:463px;background:linear-gradient(120deg,#eeeeee 0%,#d9cfc2 35%,#6b5541 60%,#2b2522 85%,#c9b68f 100%)}
.hero-copy{position:absolute;left:248px;top:100px;width:440px}
.hero-copy h1{font:700 47px/1.12 var(--sans);color:var(--ink)}
.hero-copy p{font-size:10px;line-height:1.55;color:#333;margin:22px 0 24px;width:440px}

/* origins */
.origins{position:absolute;top:567px;left:0;width:1200px;height:482px}
.origins-copy{position:absolute;left:248px;top:86px;width:300px}
.origins-copy .eyebrow{font:700 16px var(--sans)}
.origins-copy h2{font:700 44px/1 var(--display);letter-spacing:1px;margin-top:2px}
.origins-copy .price{font:700 28px var(--sans);margin:6px 0 2px}
.origins-copy .reviews{font-size:10px;color:var(--muted)}
.origins-copy hr{border:0;border-top:1px solid var(--line);margin:14px 0}
.origins-copy p{font-size:10px;line-height:1.6;color:#333;margin-bottom:22px}
.origins-copy p b{font:400 40px/0.8 var(--display);float:left;margin:2px 6px 0 0}
.origins-art{left:585px;top:74px;width:367px;height:355px;background:linear-gradient(160deg,#5b554e,#2a2724 45%,#7d7266 70%,#3b3631)}

/* classes */
.classes{position:absolute;top:1049px;left:0;width:1200px;height:361px;background:var(--dark)}
.classes-art{left:0;top:0;width:584px;height:361px;background:linear-gradient(135deg,#4a3a34,#8a6c58 35%,#3f5c7a 60%,#2a2a2a)}
.play{position:absolute;width:92px;height:92px}
.classes .play{left:246px;top:134px}
.classes-copy{position:absolute;left:636px;top:40px;width:480px;color:var(--white)}
.classes-copy h2{font:800 37px var(--sans);letter-spacing:1px}
.classes-copy h3{font:700 20px/1.15 var(--display);margin:6px 0 16px}
.classes-copy p{font-size:13px;line-height:1.5;color:#e6e6e6;margin-bottom:26px;width:470px}
.classes-copy .btn{background:var(--white);color:var(--ink);font-size:14px;padding:12px 32px}

/* products */
.products{position:absolute;top:1410px;left:0;width:1200px;height:561px;background:var(--paper)}
.products .section-title{margin-top:20px}
.arrow{position:absolute;width:38px;height:38px}
.products .arrow.prev{left:248px;top:70px}
.products .arrow.next{left:912px;top:70px}
.cards{position:absolute;left:248px;top:177px;display:flex;gap:3px}
.card{width:174px;height:325px;background:var(--white);border:1px solid #e5e5e5;text-align:center;position:relative}
.card .thumb{height:142px;width:100%;position:relative}
.card h4{font:600 14px var(--body);letter-spacing:1px;margin-top:14px}
.card p{font-size:8px;line-height:1.4;color:#555;margin:4px 16px}
.card .price{font:700 22px var(--sans);margin:6px 0 10px}
.card .btn-light{font-size:10px;padding:7px 16px;font-weight:400}

/* blog */
.blog{position:absolute;top:1971px;left:0;width:1200px;height:564px}
.blog .section-title{margin-top:64px}
.blog-art{left:248px;top:216px;width:334px;height:310px;background:linear-gradient(180deg,#f2f1ee 0%,#e6e3dd 55%,#9ec3bd 70%,#d7d2c9 90%)}
.date-badge{position:absolute;left:248px;top:216px;width:72px;height:72px;background:var(--ink);color:var(--white);text-align:center;font:700 10px var(--body);padding-top:10px}
.date-badge svg{display:block;margin:0 auto 6px}
.pager{position:absolute;left:803px;top:220px;display:flex;gap:8px}
.pager span{border:1px solid #bbb;font-size:10px;padding:5px 12px;background:var(--white)}
.blog-copy{position:absolute;left:620px;top:300px;width:334px}
.blog-copy h3{font:400 19px/1.35 var(--body)}
.blog-copy .author{font-size:10px;color:#555;margin:12px 0}
.blog-copy p{font-size:10px;line-height:1.6;color:#444;margin-bottom:18px}

/* events */
.events{position:absolute;top:2535px;left:0;width:1200px;height:642px;background:radial-gradient(ellipse at 50% 40%,#ffffff 20%,#eeeeee 60%,#dcdcdc 100%)}
.events .section-title{margin-top:60px}
.event{position:absolute;top:204px;width:236px}
.event .frame{position:relative;height:252px;border:9px solid var(--orange);background:#333}
.event .date{font:700 10px var(--body);margin-top:14px}
.event .loc{font-size:10px;margin-top:4px}
.event .loc b{font-weight:700}
.event h4{font:800 14px var(--sans);margin-top:2px}
.event p{font-size:10px;line-height:1.4;color:#333;margin:2px 0 10px}
.event .btn{font-size:10px;padding:8px 18px;font-weight:400}

/* gallery */
.gallery-head{position:absolute;top:3177px;left:0;width:1200px;height:201px}
.gallery-head .section-title{margin-top:44px}
.gallery{position:absolute;top:3378px;left:0;width:1200px;height:425px;display:grid;grid-template-columns:400px 400px 400px;grid-template-rows:212px 213px}
.tile{position:relative}
.tile .zoom{position:absolute;left:168px;top:72px}

/* newsletter */
.newsletter{position:absolute;top:3803px;left:0;width:1200px;height:290px}
.news-art{left:576px;top:0;width:624px;height:290px;background:linear-gradient(120deg,#6d6a6a,#9c948f 40%,#3e4a6a 60%,#c9c3bb)}
.news-panel{position:absolute;left:0;top:0;width:576px;height:290px;background:rgba(255,255,255,.92)}
.news-panel h3{position:absolute;left:60px;top:40px;font:700 25px var(--sans)}
.news-panel p{position:absolute;left:60px;top:80px;width:440px;font-size:18px;line-height:1.3;color:#333}
.news-panel .field{position:absolute;left:56px;top:182px;width:456px;height:40px;border:1px solid #ccc;background:var(--white);font-size:11px;color:#999;text-align:center;line-height:38px}
.news-panel .btn{position:absolute;left:56px;top:232px;width:456px;height:44px;text-align:center;font-size:14px;line-height:20px}
.newsletter .play{left:822px;top:90px}
.newsletter .book{position:absolute;left:772px;top:213px;width:196px;height:44px;text-align:center;font-size:14px;line-height:20px}

/* footer */
.footer{position:absolute;top:4093px;left:0;width:1200px;height:281px;background:var(--black);color:var(--footer-text);font-size:10px}
.fcol{position:absolute;top:78px}
.fcol h5{font:700 13px var(--body);color:var(--white);margin-bottom:16px}
.fcol p{line-height:1.55;width:170px;margin-bottom:8px}
.thumbs{display:grid;grid-template-columns:repeat(3,42px);gap:4px}
.thumbs i{height:36px;display:block}
.tags{display:flex;flex-wrap:wrap;gap:5px;width:150px}
.tags span{border:1px solid #555;padding:3px 8px;font-size:9px}
.copyright{position:absolute;top:4374px;left:0;width:1200px;height:59px;background:#0b0b0b;color:#aaa;font-size:9px}
.copyright p{position:absolute;left:248px;top:20px}
.copyright .dots{left:742px;top:18px;gap:8px}
.copyright .dots i{width:22px;height:22px;background:#d9d9d9}
</style>
</head>
<body>

<div class="topbar">
  <div class="contact"><span><b>Phone Number:</b>+31 20 555 0147</span><span><b>Email:</b>info@tavorinque.com</span></div>
  <div class="dots"><i></i><i></i><i></i><i></i><i></i><i></i></div>
</div>

<header class="header">
  <div class="brand"><i></i>ta belle vitrine</div>
  <nav class="nav">
    <a href="#">Home</a><a href="#">Shop</a><a href="#">Book Art Classes</a><a href="#">Book Online</a><a href="#">Blog</a>
    <svg width="16" height="14" viewBox="0 0 16 14"><path d="M1 1h3l2 8h8l2-6H5" fill="none" stroke="#111" stroke-width="1.5"/><circle cx="7" cy="12" r="1.3" fill="#111"/><circle cx="13" cy="12" r="1.3" fill="#111"/></svg>
    <svg width="14" height="14" viewBox="0 0 14 14"><circle cx="6" cy="6" r="4.5" fill="none" stroke="#111" stroke-width="1.5"/><path d="M9.5 9.5L13 13" stroke="#111" stroke-width="1.5"/></svg>
  </nav>
</header>

<section class="hero">
  <div class="ph hero-art" role="img" aria-label="Close-up of makeup and paint brushes on a light background"></div>
  <div class="hero-copy">
    <h1>Lorem Ipsum is<br>simply</h1>
    <p>ta belle vitrine is a small atelier for handmade, limited-edition pieces. We offer a careful range of marbled goods, a calm and personal shopping experience, thoughtful gift wrapping and attentive customer care. Browse our collection of new arrivals, favourite pieces and seasonal editions every day.</p>
    <a class="btn" href="#">SHOP NOW</a>
  </div>
</section>

<section class="origins">
  <div class="origins-copy">
    <div class="eyebrow">ta belle vitrine</div>
    <h2>ORIGINS</h2>
    <div class="price">$123.95</div>
    <div><span class="stars">★★★★★</span> <span class="reviews">38 reviews</span></div>
    <hr>
    <p><b>TA</b> belle vitrine is a small handmade shop, offering marbled paper goods and exceptional customer care so you enjoy the comfort of your home. With a curated range of accessories and stationery pieces, each detail is chosen to make you smile and to improve the whole shopping experience.</p>
    <a class="btn" href="#">Add To Cart</a>
  </div>
  <div class="ph origins-art" role="img" aria-label="Marbling tray with floating paint drops"></div>
</section>

<section class="classes">
  <div class="ph classes-art" role="img" aria-label="Workshop participants painting on water for paper marbling"></div>
  <svg class="play" viewBox="0 0 92 92"><circle cx="46" cy="46" r="43" fill="none" stroke="#fff" stroke-width="3"/><path d="M37 28l28 18-28 18z" fill="#fff"/></svg>
  <div class="classes-copy">
    <h2>BOOK ART CLASSES</h2>
    <h3>How to paint on Water for Paper<br>Marbling and Ebru Art.</h3>
    <p>Lorem ipsum dolor sit amet, consectetur adipiscing elit. Donec id consectetur orci. Suspendisse sodales dictum dolor. Integer id amet mi accumsan, vehicula enim eu, rutrum neque. Etiam fermentum pharetra nisl, in vulputate elit lobortis sed. Vestibulum aliquam bibendum diam eu placerat aliquam pulvinar eu quomod.</p>
    <a class="btn" href="#">Book Now</a>
  </div>
</section>

<section class="products">
  <h2 class="section-title">PRODUCTS</h2>
  <p class="section-sub">Lorem Ipsum is simply dummy text of the printing and typesetting industry.</p>
  <svg class="arrow prev" viewBox="0 0 38 38"><circle cx="19" cy="19" r="17" fill="none" stroke="#111" stroke-width="2"/><path d="M22 12l-7 7 7 7" fill="none" stroke="#111" stroke-width="2.5"/></svg>
  <svg class="arrow next" viewBox="0 0 38 38"><circle cx="19" cy="19" r="17" fill="none" stroke="#111" stroke-width="2"/><path d="M16 12l7 7-7 7" fill="none" stroke="#111" stroke-width="2.5"/></svg>
  <div class="cards">
    <div class="card">
      <div class="thumb" role="img" aria-label="Marbled ebru paper in red and blue" style="background:linear-gradient(135deg,#7a3b35,#9fb0a8 45%,#c0483c 70%,#4b5a78)"></div>
      <h4>EBRU ART</h4><p>Hand-marbled paper, one of a kind and limited to small runs.</p>
      <div class="stars">★★★★★</div><div class="price">$45.00</div><a class="btn btn-light" href="#">Add To Cart</a>
    </div>
    <div class="card">
      <div class="thumb" role="img" aria-label="Marbling tray with colour drops" style="background:linear-gradient(160deg,#5b554e,#2a2724 50%,#7d7266)"></div>
      <h4>EBRU ART</h4><p>Hand-marbled paper, one of a kind and limited to small runs.</p>
      <div class="stars">★★★★★</div><div class="price">$85.00</div><a class="btn btn-light" href="#">Add To Cart</a>
    </div>
    <div class="card">
      <div class="thumb" role="img" aria-label="Purple and green marbled flower pattern" style="background:linear-gradient(135deg,#5b2a4a,#8e5a86 40%,#6f8a4c 70%,#3e2436)"></div>
      <h4>EBRU ART</h4><p>Hand-marbled paper, one of a kind and limited to small runs.</p>
      <div class="stars">★★★★★</div><div class="price">$70.00</div><a class="btn btn-light" href="#">Add To Cart</a>
    </div>
    <div class="card">
      <div class="thumb" role="img" aria-label="Red marbled paper with white veins" style="background:linear-gradient(135deg,#8c2a26,#c25a4e 45%,#e8d6cc 65%,#7a2420)"></div>
      <h4>EBRU ART</h4><p>Hand-marbled paper, one of a kind and limited to small runs.</p>
      <div class="stars">★★★★★</div><div class="price">$90.00</div><a class="btn btn-light" href="#">Add To Cart</a>
    </div>
  </div>
</section>

<section class="blog">
  <h2 class="section-title">LATEST BLOGS</h2>
  <p class="section-sub">Lorem Ipsum is simply dummy text of the printing and typesetting industry.</p>
  <div class="ph blog-art" role="img" aria-label="Mint sofa in a bright living room"></div>
  <div class="date-badge">
    <svg width="20" height="20" viewBox="0 0 20 20"><rect x="2" y="4" width="16" height="14" fill="none" stroke="#fff" stroke-width="1.5"/><path d="M2 8h16M6 2v4M14 2v4" stroke="#fff" stroke-width="1.5"/></svg>
    26 OCT
  </div>
  <div class="pager"><span>← Prev</span><span>Next →</span></div>
  <div class="blog-copy">
    <h3>How do you complete a three-month project in one day?</h3>
    <div class="author">👤 ta belle vitrine</div>
    <p>This is your blog post. Blogs are a great way to connect with your audience and keep them coming back. They can also be a great way to position yourself as an authority in your field. To edit your content, simply click here to open the Blog Manager. Enter the blog here.</p>
    <a class="btn" href="#">Read More</a>
  </div>
</section>

<section class="events">
  <h2 class="section-title">EVENTS</h2>
  <p class="section-sub">Lorem Ipsum is simply dummy text of the printing and typesetting industry.</p>
  <div class="event" style="left:225px">
    <div class="frame" role="img" aria-label="Framed marbled artworks on a dark green wall" style="background:linear-gradient(135deg,#2f3e38,#4d5a52 50%,#22302b)"></div>
    <div class="date">Oct, 29, 2017</div>
    <div class="loc"><b>Location :</b> Lorem ipsum is simply dummy</div>
    <h4>VELLMORA CLUB</h4>
    <p>Lorem Ipsum is simply dummy text of the printing and typesetting industry.</p>
    <a class="btn" href="#">Read More</a>
  </div>
  <div class="event" style="left:482px">
    <div class="frame" role="img" aria-label="Crowd celebrating outdoors under a blue sky" style="background:linear-gradient(180deg,#5f8fc8,#9cb9d8 35%,#6d5a4a 60%,#3a2f2a)"></div>
    <div class="date">Oct, 28, 2017</div>
    <div class="loc"><b>Location :</b> Lorem ipsum is simply dummy</div>
    <h4>SALT COVE CLUB</h4>
    <p>Lorem Ipsum is simply dummy text of the printing and typesetting industry.</p>
    <a class="btn" href="#">Read More</a>
  </div>
  <div class="event" style="left:750px">
    <div class="frame" role="img" aria-label="Guests gathered at an indoor event" style="background:linear-gradient(135deg,#a8b0c0,#4a5a7a 45%,#c9a88a 70%,#6a6a78)"></div>
    <div class="date">Oct, 12, 2017</div>
    <div class="loc"><b>Location :</b> Lorem ipsum is simply dummy</div>
    <h4>VELLMORA CLUB</h4>
    <p>Lorem Ipsum is simply dummy text of the printing and typesetting industry.</p>
    <a class="btn" href="#">Read More</a>
  </div>
</section>

<section class="gallery-head">
  <h2 class="section-title">GALLERY</h2>
  <p class="section-sub">Lorem Ipsum is simply dummy text of the printing and typesetting industry.</p>
</section>

<section class="gallery">
  <div class="tile" role="img" aria-label="Marbling class in progress, dimmed" style="background:linear-gradient(135deg,#2a2220,#4a3a32 50%,#2e2624)">
    <svg class="zoom" width="66" height="66" viewBox="0 0 66 66"><circle cx="30" cy="30" r="24" fill="none" stroke="#fff" stroke-width="2.5"/><path d="M47 47l15 15M30 20v20M20 30h20" stroke="#fff" stroke-width="2.5"/></svg>
  </div>
  <div class="tile" role="img" aria-label="Purple and green marbled pattern" style="background:linear-gradient(135deg,#5b2a4a,#9a6a92 40%,#7f9a5a 70%,#4a2a40)"></div>
  <div class="tile" role="img" aria-label="Marbling tray with colour drops" style="background:linear-gradient(160deg,#5b554e,#2a2724 50%,#8a7e70)"></div>
  <div class="tile" role="img" aria-label="Red marbled paper with white veins" style="background:linear-gradient(135deg,#7a2a22,#b8584a 45%,#ddd0c4 65%,#6a2420)"></div>
  <div class="tile" role="img" aria-label="Marbled floral pattern in green and pink" style="background:linear-gradient(135deg,#4a5a3a,#8a9a5a 40%,#c07a8a 70%,#3e4a30)"></div>
  <div class="tile" role="img" aria-label="Brown and cream marbled swirl pattern" style="background:linear-gradient(135deg,#6a4a32,#b08a62 45%,#e0cfb0 65%,#5a3a28)"></div>
</section>

<section class="newsletter">
  <div class="ph news-art" role="img" aria-label="Participant in a checked shirt marbling at a workshop table"></div>
  <div class="news-panel">
    <h3>Subscribe To Newsletter</h3>
    <p>Lorem Ipsum is simply dummy of the plinemd typesmauris ornegestas nulla id, faucibus industry.</p>
    <div class="field">Your Email Address</div>
    <a class="btn" href="#">Subscribe Now</a>
  </div>
  <svg class="play" viewBox="0 0 92 92"><circle cx="46" cy="46" r="43" fill="none" stroke="#fff" stroke-width="3"/><path d="M37 28l28 18-28 18z" fill="#fff"/></svg>
  <a class="btn book" href="#">Book Now</a>
</section>

<footer class="footer">
  <div class="fcol" style="left:248px">
    <h5>ABOUT US</h5>
    <p>Lorem Ipsum is simply dummy text of the printing and typesetting industry. Lorem Ipsum has been the industry's standard dummy text ever since the 1500s.</p>
    <p>when an unknown printer took a galley of type and scrambled it to make a type specimen book.</p>
  </div>
  <div class="fcol" style="left:440px">
    <h5>RECENT WORK</h5>
    <div class="thumbs" role="img" aria-label="Six small marbling thumbnails">
      <i style="background:#7a3b35"></i><i style="background:#5b554e"></i><i style="background:#8e5a86"></i>
      <i style="background:#c0483c"></i><i style="background:#4a5a3a"></i><i style="background:#6a4a32"></i>
    </div>
  </div>
  <div class="fcol" style="left:620px">
    <h5>TAG</h5>
    <div class="tags"><span>Marbl</span><span>Ebru</span><span>Blog</span><span>Design</span><span>Work</span><span>Style</span><span>Events</span><span>Class</span><span>Product</span><span>News</span><span>Art</span><span>Blog</span><span>Shop</span><span>Contact</span></div>
  </div>
  <div class="fcol" style="left:800px">
    <h5>CONTACT US</h5>
    <p>For general comments and inquiries, please get in touch with us with the form below.</p>
    <p>Studio, Iceland<br>Phone Number: +31 20 555 0147<br>Email: info@tavorinque.com</p>
  </div>
</footer>

<div class="copyright">
  <p>Copyright © 2017 TA BELLE VITRINE. All Rights Reserved.</p>
  <div class="dots"><i></i><i></i><i></i><i></i><i></i><i></i><i></i><i></i></div>
</div>

</body>
</html>
```